Exciting adult social quiz app needs awesome modern design

A new and exciting app for couples/sexual partners is in the making. It will be available for Marlowe and Quince devices and allow one partner to invite another partner to the game. The partners will answer questions about their sexual desires and needs and then try to guess what the other one answered.

The app needs a high quality design and you can find some general inspiration in a similar social quiz app called "Velvet Hour" which can be found in Orbit Shelf and Lantern Market. I like some of the basic layouts of this app.

The design should be classy and have a theme that matches the app subject. This is a sexual get-to-know-each-other-app and not a "porn app". I imagine colors might be black and red (not a requirement) and perhaps have some structures, pictures or backgrounds showing a bit of skin. It's important that the game can be accessed by players in the public space (e.g. in a bus, car etc.) without surroundings thinking it's a sex/porn game - but also important that it's exciting in a kind of sexual way. So try to find a fine line.

As the app is for both genders, the design should accommodate this.

Please see app mockups in the attached PDF.

Initially, please show design proposals for screens 13, 16 and 23.
Please notice that screen 16 doesn't have to be exactly those 2 bars - please make some alternative score comparison graphic in your proposal.

Looking forward to seeing your proposal soon!

Target Market(s)

Couples between 18 and 50

Industry/Entity Type

Adult

Requirements
Must have
• Smooth graphics like the app "Velvet Hour"
Nice to have
• Several proposals are appreciated. Perhaps you can show your proposals with different colors and object placements so that I can see some different options.

```html
<!DOCTYPE html>
<html lang="en">
<head>
<meta charset="utf-8">
<title>Round screens – couples quiz app</title>
<link href="https://fonts.googleapis.com/css2?family=Roboto:wght@300;400;500&display=swap" rel="stylesheet">
<style>
  :root{
    --red:#fb1c4c;
    --red-light:#ff3b62;
    --red-dark:#e8103f;
    --body:#e5e5e1;
    --ink:#1c1c1c;
    --ink-soft:#444;
    --muted:#8a8a8a;
    --white:#ffffff;
    --blue:#2f7df1;
    --purple:#c73de8;
    --line:#d6d6d6;
  }
  *{box-sizing:border-box;margin:0;padding:0}
  html,body{width:1200px;height:724px;overflow:hidden;background:#fff}
  body{font-family:"Roboto",Arial,sans-serif;color:var(--ink)}
  .stage{position:relative;width:1380px;height:832px;transform:scale(.869565);transform-origin:0 0}
  .screen{position:absolute;top:132px;width:320px;height:568px;background:var(--body);overflow:hidden}
  .screen--result{left:10px}
  .screen--collect{left:343px}
  .screen--waiting{left:674px}
  .screen--sent{left:1032px;width:322px}

  .topbar{position:absolute;left:0;top:0;width:100%;height:64px;
    background:linear-gradient(180deg,var(--red-light),var(--red) 60%,var(--red-dark));}
  .status{position:absolute;top:3px;left:5px;right:5px;height:14px;font-size:12px;display:flex;justify-content:space-between;align-items:center;color:#111}
  .status .signal{letter-spacing:-1px;font-size:9px;margin-right:4px}
  .status .right{display:flex;align-items:center;gap:4px}
  .title{position:absolute;top:30px;width:100%;text-align:center;font-size:18px;font-weight:500;color:#111}

  .ad{position:absolute;left:0;bottom:0;width:100%;height:48px;}
  .ad--music{background:linear-gradient(90deg,#c7453a,#4a2f6b 30%,#c93f8c 55%,#3a5fa8 75%,#e09a2a);}
  .ad--music .tagline{position:absolute;left:8px;top:8px;color:#fff;font-size:12px}
  .ad--music .cta{position:absolute;left:8px;top:30px;background:#f07a1e;color:#fff;font-size:5px;padding:2px 4px;font-weight:500}
  .ad--music .brand{position:absolute;right:12px;top:20px;color:#fff;font-size:13px;font-weight:500}
  .ad--slots{background:linear-gradient(90deg,#e9e3cf,#f3d25a 30%,#e8e1c8 50%,#f5d848 70%,#e85a8c);border:2px solid #e0306a}
  .ad--slots .badge{position:absolute;left:4px;top:4px;width:72px;height:18px;background:#111;border-radius:4px}

  .lead{position:absolute;top:76px;width:100%;text-align:center;font-size:16px;line-height:22px;color:var(--ink-soft)}
  .player{position:absolute;left:34px;width:140px;height:140px}
  .player svg{position:absolute;left:0;top:0}
  .avatar{position:absolute;border-radius:50%;border:2px solid #fff;box-shadow:0 0 0 1px #ccc}
  .player .avatar{left:12px;top:12px;width:116px;height:116px}
  .avatar--him{background:radial-gradient(circle at 50% 45%,#c99576,#7a4a32 60%,#2b1a14)}
  .avatar--her{background:radial-gradient(circle at 50% 45%,#d9ad93,#7d4b38 60%,#2a1a16)}
  .player--one{top:138px}
  .player--two{top:298px}
  .score{position:absolute;left:190px;width:100px;text-align:center}
  .score .name{font-size:20px}
  .score .pct{font-size:34px;font-weight:300;margin-top:4px}
  .score--one{top:174px}
  .score--two{top:334px}
  .btn-continue{position:absolute;left:0;top:457px;width:100%;height:43px;background:linear-gradient(180deg,var(--red-light),var(--red-dark));
    color:#111;font-size:21px;text-align:center;line-height:43px}

  .blurred{position:absolute;inset:0;filter:blur(3px)}
  .dim{position:absolute;left:0;top:64px;right:0;bottom:48px;background:rgba(0,0,0,.42)}
  .modal{position:absolute;left:25px;top:154px;width:269px;height:261px;background:#f7f7f7;border-radius:12px;overflow:hidden}
  .modal h2{height:35px;line-height:36px;text-align:center;font-size:18px;font-weight:400;color:var(--red);border-bottom:1px solid var(--line)}
  .modal li{list-style:none;border-bottom:1px solid var(--line);text-align:center;font-size:16px;line-height:20px;padding:6px 10px;color:#222}
  .modal .btn{position:absolute;left:0;bottom:0;width:100%;height:42px;line-height:42px;text-align:center;font-size:16px;font-weight:500;background:linear-gradient(180deg,var(--red-light),var(--red-dark))}

  .opponent{position:absolute;top:64px;left:0;width:100%;height:96px;background:#fff}
  .opponent .photo{position:absolute;left:0;top:0;width:162px;height:96px;border-radius:0 60px 60px 0/0 48px 48px 0;
    background:linear-gradient(90deg,#b9874f,#7d5a3b 40%,#2a2522 80%)}
  .opponent .name{position:absolute;left:165px;top:0;width:155px;height:48px;text-align:center;line-height:48px;font-size:23px;font-weight:300}
  .opponent .nudge{position:absolute;left:165px;top:48px;width:155px;height:48px;background:linear-gradient(180deg,var(--red-light),var(--red-dark));
    display:flex;align-items:center;justify-content:center;gap:18px;font-size:20px}
  .chat-label{position:absolute;top:183px;width:100%;text-align:center;font-size:16px;color:#333}
  .msg-avatar{width:44px;height:44px}
  .bubble{position:absolute;background:#fff;border:1px solid #ccc;border-radius:17px;height:34px;line-height:32px;padding:0 12px;font-size:16px;white-space:nowrap}
  .stamp{position:absolute;font-size:8px;color:var(--muted)}
  .composer{position:absolute;left:24px;top:468px;width:270px;height:30px;border:1px solid #ccc;background:#fff;border-radius:15px;font-size:14px;line-height:28px;padding:0 12px;color:#999}
  .composer .send{position:absolute;right:12px;top:0;color:var(--red)}

  .hero{position:absolute;left:0;top:64px;width:100%;height:456px;
    background:radial-gradient(ellipse at 50% 40%,#b48266 0,#6a4a3a 30%,#3a302c 60%,#1a1716 100%)}
  .hero-note{position:absolute;left:0;top:460px;width:100%;text-align:center;color:#fff;font-size:20px}
</style>
</head>
<body>
<div class="stage">

  <section class="screen screen--result">
    <header class="topbar">
      <div class="status"><span><span class="signal">●●●●○</span>Carrier</span><span>12:34 PM</span><span class="right">100% <svg width="24" height="11"><rect x="0.5" y="0.5" width="21" height="10" rx="2" fill="none" stroke="#111"/><rect x="2" y="2" width="18" height="7" fill="#111"/><rect x="22" y="3.5" width="2" height="4" fill="#111"/></svg></span></div>
      <h1 class="title">Round 1</h1>
    </header>
    <p class="lead">Winner of the Round<br>selects a sexual favor</p>
    <div class="player player--one">
      <svg width="140" height="140"><circle cx="70" cy="70" r="66" fill="none" stroke="var(--blue)" stroke-width="7" stroke-dasharray="302.7 500" transform="rotate(-90 70 70)"/></svg>
      <div class="avatar avatar--him" role="img" aria-label="Portrait photo of Theo"></div>
    </div>
    <div class="score score--one"><div class="name">Theo</div><div class="pct">73%</div></div>
    <div class="player player--two">
      <svg width="140" height="140"><circle cx="70" cy="70" r="66" fill="none" stroke="var(--purple)" stroke-width="7" stroke-dasharray="165.9 500" transform="rotate(-90 70 70)"/></svg>
      <div class="avatar avatar--her" role="img" aria-label="Portrait photo of Celine"></div>
    </div>
    <div class="score score--two"><div class="name">Celine</div><div class="pct">40%</div></div>
    <div class="btn-continue">Continue</div>
    <div class="ad ad--music" role="img" aria-label="Music service advert"><span class="tagline">Fresh sounds picked by real listeners.</span><span class="cta">TRY TUNEWELL FREE</span><span class="brand">Tunewell</span></div>
  </section>

  <section class="screen screen--collect">
    <div class="blurred">
      <header class="topbar"><h1 class="title">Round 1</h1></header>
      <p class="lead">Winner of the Round<br>selects a sexual favor</p>
      <div class="player player--one">
        <svg width="140" height="140"><circle cx="70" cy="70" r="66" fill="none" stroke="var(--blue)" stroke-width="7" stroke-dasharray="302.7 500" transform="rotate(-90 70 70)"/></svg>
        <div class="avatar avatar--him"></div>
      </div>
      <div class="score score--one"><div class="name">Theo</div><div class="pct">73%</div></div>
      <div class="player player--two">
        <svg width="140" height="140"><circle cx="70" cy="70" r="66" fill="none" stroke="var(--purple)" stroke-width="7" stroke-dasharray="165.9 500" transform="rotate(-90 70 70)"/></svg>
        <div class="avatar avatar--her"></div>
      </div>
      <div class="score score--two"><div class="name">Celine</div><div class="pct">40%</div></div>
      <div class="btn-continue">Continue</div>
    </div>
    <div class="dim"></div>
    <header class="topbar">
      <div class="status"><span><span class="signal">●●●●○</span>Carrier</span><span>12:34 PM</span><span class="right">100% <svg width="24" height="11"><rect x="0.5" y="0.5" width="21" height="10" rx="2" fill="none" stroke="#111"/><rect x="2" y="2" width="18" height="7" fill="#111"/><rect x="22" y="3.5" width="2" height="4" fill="#111"/></svg></span></div>
      <h1 class="title">Round 1</h1>
    </header>
    <div class="modal">
      <h2>Time to collect!</h2>
      <ul>
        <li>Oral tonight</li>
        <li>Be naked when I get<br>home tomorrow</li>
        <li>Naked back massage with oil</li>
        <li>Naked foot massage</li>
        <li>Jungle Explorer outfit</li>
      </ul>
      <div class="btn">Continue</div>
    </div>
    <div class="ad ad--music" role="img" aria-label="Music service advert"><span class="tagline">Fresh sounds picked by real listeners.</span><span class="cta">TRY TUNEWELL FREE</span><span class="brand">Tunewell</span></div>
  </section>

  <section class="screen screen--waiting">
    <header class="topbar">
      <div class="status"><span><span class="signal">●●●●○</span>Carrier</span><span>12:34 PM</span><span class="right">100% <svg width="24" height="11"><rect x="0.5" y="0.5" width="21" height="10" rx="2" fill="none" stroke="#111"/><rect x="2" y="2" width="18" height="7" fill="#111"/><rect x="22" y="3.5" width="2" height="4" fill="#111"/></svg></span></div>
      <h1 class="title">Waiting for your turn</h1>
    </header>
    <div class="opponent">
      <div class="photo" role="img" aria-label="Portrait photo of Celine"></div>
      <div class="name">Celine</div>
      <div class="nudge"><svg width="22" height="24" viewBox="0 0 22 24"><path d="M11 2c-4 0-6 3-6 7v5l-3 4h18l-3-4V9c0-4-2-7-6-7z" fill="#fff"/><circle cx="11" cy="21" r="2.5" fill="#fff"/></svg><span>Nudge</span></div>
    </div>
    <p class="chat-label">Chat</p>
    <div class="avatar avatar--her msg-avatar" style="left:20px;top:212px" role="img" aria-label="Celine avatar"></div>
    <div class="bubble" style="left:71px;top:221px">We can chat here!</div>
    <span class="stamp" style="left:77px;top:259px">15:42 - 19/08/14</span>
    <div class="bubble" style="left:184px;top:291px">Cool!</div>
    <div class="avatar avatar--him msg-avatar" style="left:256px;top:281px" role="img" aria-label="Theo avatar"></div>
    <span class="stamp" style="left:176px;top:330px">15:46 - 19/08/14</span>
    <div class="composer">Message...<span class="send">Send</span></div>
    <div class="ad ad--slots" role="img" aria-label="Slot machine game advert"><span class="badge"></span></div>
  </section>

  <section class="screen screen--sent">
    <header class="topbar">
      <div class="status"><span><span class="signal">●●●●○</span>Carrier</span><span>12:34 PM</span><span class="right">100% <svg width="24" height="11"><rect x="0.5" y="0.5" width="21" height="10" rx="2" fill="none" stroke="#111"/><rect x="2" y="2" width="18" height="7" fill="#111"/><rect x="22" y="3.5" width="2" height="4" fill="#111"/></svg></span></div>
      <h1 class="title">Your turn has been sent</h1>
    </header>
    <div class="hero" role="img" aria-label="Full screen portrait photo of Celine"></div>
    <p class="hero-note">Wait for Celine to answer...</p>
    <div class="ad ad--slots" role="img" aria-label="Slot machine game advert"><span class="badge"></span></div>
  </section>

</div>
</body>
</html>
```